Velk Partners Building Business Cards

We need a business card that reflects our business as "Solar Experts" in San Diego. Browse our website www.velkpartners.example our License needs to be displayed as "CSLB# 3867140" our phone number is (619) 555-0187

Save thousands on your electric bills and increase the value of your home while helping to protect the environment. Our solar installation experts will help you design the system that's right for you, using only the highest quality equipment that will look great and give you ideal performance. Our goal is to make you energy independent, and get your electric bill to 0.

Paul Osterby
(619) 555-0187
paul@velkpartners.example

Target Market(s)

Home owners in san diego looking for solar

Industry/Entity Type

Solar Energy

Contact Information for Business Card

Paul Osterby
(619) 555-0187
paul@velkpartners.example

Font styles to use
Other font styles liked:
• Use our logo font

Requirements
Must have
• License needs to be displayed as "CSLB# 3867140" our phone number is (619) 555-0187
Nice to have
• Real images of rooftop home solar in san diego
Should not have
• our business address

```html
<!DOCTYPE html>
<html lang="en">
<head>
<meta charset="utf-8">
<title>Velk Partners Building – Business Cards</title>
<link rel="stylesheet" href="https://fonts.googleapis.com/css2?family=Open+Sans:wght@400;600;700&family=Cinzel:wght@400&display=swap">
<style>
  :root {
    --stage-top: #1b1b1b;
    --stage-bottom: #050505;
    --card: #ffffff;
    --card-back: #fcfcfc;
    --navy: #1d3a78;
    --sun: #f6b20f;
    --ink: #2b2b2b;
  }
  * { box-sizing: border-box; margin: 0; padding: 0; }
  html, body {
    width: 1200px;
    height: 900px;
    overflow: hidden;
  }
  body {
    position: relative;
    background: linear-gradient(180deg, var(--stage-top) 0%, #101010 55%, var(--stage-bottom) 100%);
    font-family: "Open Sans", Arial, sans-serif;
  }
  .card {
    position: absolute;
    top: 306px;
    width: 440px;
    height: 271px;
    border-radius: 10px;
    background: var(--card);
  }
  .card--front { left: 149px; }
  .card--back { left: 608px; background: var(--card-back); }

  .brand-mark {
    position: absolute;
    left: 44px;
    top: 112px;
    display: flex;
    align-items: center;
    gap: 10px;
  }
  .brand-mark__dot {
    width: 36px;
    height: 36px;
    border-radius: 50%;
    background: var(--sun);
    flex: none;
  }
  .brand-mark__name {
    font-weight: 700;
    font-size: 16px;
    line-height: 1.2;
    color: var(--navy);
    width: 120px;
  }

  .contact {
    position: absolute;
    left: 240px;
    top: 85px;
    color: var(--ink);
    font-size: 12px;
  }
  .contact__name {
    font-weight: 600;
    font-size: 14.5px;
    line-height: 20px;
    color: var(--navy);
    margin-bottom: 22px;
  }
  .contact__license { margin-bottom: 8px; line-height: 18px; }
  .contact__license strong { font-weight: 600; color: var(--navy); font-size: 12.5px; }
  .contact__line {
    display: flex;
    align-items: center;
    gap: 8px;
    line-height: 16px;
  }
  .contact__line svg { width: 8px; height: 8px; fill: var(--navy); flex: none; }

  .wordmark {
    position: absolute;
    left: 0;
    right: 0;
    top: 102px;
    text-align: center;
  }
  .wordmark__name {
    font-weight: 700;
    font-size: 30px;
    line-height: 38px;
    letter-spacing: -0.6px;
    color: var(--navy);
  }
  .wordmark__sub {
    font-family: "Cinzel", Georgia, serif;
    font-weight: 400;
    font-size: 20px;
    line-height: 24px;
    letter-spacing: 0.5px;
    color: var(--sun);
  }
</style>
</head>
<body>
  <section class="card card--front" aria-label="Card front">
    <div class="brand-mark">
      <span class="brand-mark__dot"></span>
      <span class="brand-mark__name">Velk Partners Building</span>
    </div>
    <div class="contact">
      <p class="contact__name">Paul Osterby</p>
      <p class="contact__license"><strong>License:</strong> CSLB# 3867140</p>
      <p class="contact__line">
        <svg viewBox="0 0 10 10" aria-hidden="true"><path d="M2 0.5 L3.6 2.6 L2.7 3.6 Q3.8 5.9 6.4 7.3 L7.4 6.4 L9.5 8 L8.4 9.5 Q4.6 9.2 1.5 5.6 Q0.3 3.8 0.5 1.6 Z"/></svg>
        (619) 555-0187
      </p>
      <p class="contact__line">
        <svg viewBox="0 0 10 10" aria-hidden="true"><path d="M0 2 H10 V8.5 H0 Z M0.8 2.6 L5 5.6 L9.2 2.6 V3.2 L5 6.2 L0.8 3.2 Z" fill-rule="evenodd"/></svg>
        paul@velkpartners.example
      </p>
    </div>
  </section>

  <section class="card card--back" aria-label="Card back">
    <div class="wordmark">
      <p class="wordmark__name">Velk Partners Building</p>
      <p class="wordmark__sub">Incorporated</p>
    </div>
  </section>
</body>
</html>
```